Etikett für Rotweinflasche
Liebe farbkosmos Atelier, wir werden uns bei der endgültigen Etikettengestaltung (finale Größe + Rückseite) noch an Euch melden. Bitte sendet uns euren Kontakt an helga.brandt@morvelli.wine
Zielgruppe
Morvelli Italia ist ein exklusives Boutique-Weingut in Sizilien, das hochqualitative Spitzenweine in kleinen Mengen mit modernster Technologie und stets nachhaltig erzeugt. Wir hinterfragen sowohl in der Agronomie im Weingarten als auch in der Önologie im Weinkeller alle herrschenden Traditionen und trachten danach, stets das beste Endprodukt zu kreieren. Der vulkanische, kalkreiche Boden Siziliens sowie trockene, sonnenreiche und niederschlagsarme Vegetationsperioden sind unsere optimale Basis.
Zielgruppe: Internationale Genussmenschen jeglichen Alters, die sich bewusst auch höherpreisige Weine (um die €30+) gönnen , vor allem kunstaffine young professionals mit Qualitäts-& Nachhaltigkeitsanspruch
Aufgabenstellung
Das Etikett ist für Rotwein-Flaschen (Cabernet Sauvignon / Nero D'Avola / Frappato / Syrah / Cerasuolo / Petit Verdot / sowie einen Bourdeaux-Cuveè aus Cabernet Sauvignon und Petit Verdot) .
Die Flasche ist reinschwarz, sehr hochwertig und schwer.
Flaschenform: Bordeauxflasche siehe technisches Datenblatt
Sleeve über dem Korken: schwarz mit weißer Schrift wie bisher
Zu gestalten ist das Etikett der Vorderseite. Zumindest die jeweilige Rotwein-Sorte ist auch textlich darzustellen (zwecks Scannen mit Trubel-App)
Der Kreativität kann freien Lauf gelassen werden! Unterscheidbarkeit vom Markt ist explizit gewollt.
Unsere aktuellen Etiketten und Markenauftritt siehe: https://morvelli.wine/shop/

```html
<!DOCTYPE html>
<html lang="de">
<head>
<meta charset="utf-8">
<title>Etikettenserie Rotwein</title>
<link rel="stylesheet" href="https://fonts.googleapis.com/css2?family=Anton&display=swap">
<style>
  :root {
    --stage: #0a0003;
    --ink: #f3b7a2;
    --core: #d24e3a;
    --cerasuolo-edge: #e27b30;
    --verdot-edge: #5a6b51;
    --cuvee-edge: #d59b85;
    --cuvee-core: #d0523f;
    --nero-edge: #3a3837;
    --syrah-edge: #bb3136;
    --syrah-core: #d44c3b;
    --frappato-edge: #6f4a85;
    --drop: rgba(245, 216, 200, 0.22);
  }
  * { margin: 0; padding: 0; box-sizing: border-box; }
  html, body { width: 1200px; height: 675px; overflow: hidden; background: var(--stage); }
  .series { position: relative; width: 1200px; height: 675px; }
  .label {
    position: absolute;
    width: 197px;
    height: 278px;
    overflow: hidden;
    background: radial-gradient(ellipse 62% 58% at 40% 52%, var(--core) 0%, var(--core) 35%, var(--edge) 100%);
  }
  .label--cerasuolo { left: 235px; top: 30px; --edge: var(--cerasuolo-edge); }
  .label--verdot    { left: 501px; top: 30px; --edge: var(--verdot-edge); }
  .label--cuvee     { left: 769px; top: 30px; --edge: var(--cuvee-edge); --core: var(--cuvee-core); }
  .label--nero      { left: 235px; top: 366px; --edge: var(--nero-edge); }
  .label--syrah     { left: 501px; top: 366px; --edge: var(--syrah-edge); --core: var(--syrah-core); }
  .label--frappato  { left: 769px; top: 366px; --edge: var(--frappato-edge); }

  .drops {
    position: absolute;
    left: 45px; top: 40px;
    width: 75px; height: 198px;
    background: radial-gradient(ellipse 60% 50% at 50% 45%, var(--drop), rgba(245, 216, 200, 0) 100%);
  }
  .variety {
    position: absolute;
    right: 21px;
    top: 139px;
    writing-mode: vertical-rl;
    transform: translateY(-50%) rotate(180deg);
    font-family: "Anton", "Oswald", sans-serif;
    font-size: 27px;
    font-weight: 400;
    line-height: 1.12;
    letter-spacing: 0.01em;
    text-align: center;
    text-transform: uppercase;
    color: var(--ink);
    opacity: 0.88;
    white-space: nowrap;
  }
  .label--cuvee .variety { opacity: 0.6; right: 22px; }
</style>
</head>
<body>
<main class="series">
  <article class="label label--cerasuolo">
    <div class="drops" role="img" aria-label="Abstrakte Tropfenformen in Creme"></div>
    <h2 class="variety">Cerasuolo</h2>
  </article>
  <article class="label label--verdot">
    <div class="drops" role="img" aria-label="Abstrakte Tropfenformen in Creme"></div>
    <h2 class="variety">Petit<br>Verdot</h2>
  </article>
  <article class="label label--cuvee">
    <div class="drops" role="img" aria-label="Abstrakte Tropfenformen in Creme"></div>
    <h2 class="variety">Bourdeaux-Cuvée<br>Cabernet Sauvignon<br>&amp; Petit Verdot</h2>
  </article>
  <article class="label label--nero">
    <div class="drops" role="img" aria-label="Abstrakte Tropfenformen in Creme"></div>
    <h2 class="variety">Nero<br>D'Avola</h2>
  </article>
  <article class="label label--syrah">
    <div class="drops" role="img" aria-label="Abstrakte Tropfenformen in Creme"></div>
    <h2 class="variety">Syrah</h2>
  </article>
  <article class="label label--frappato">
    <div class="drops" role="img" aria-label="Abstrakte Tropfenformen in Creme"></div>
    <h2 class="variety">Frappato</h2>
  </article>
</main>
</body>
</html>
```